Website Design For Tessel Hub Project

www.tesselhub.com.au

As the name suggests i would like to have a design for this website... the website is nothing to do with night life or parties, but it is do everything to do with being online all the time, being available 24/7.

all information needed regarding anything to do with this City and its businesses. so, Basically This will be an online business directory for local businesses. What i am looking for is a website that can display Business listings in a pleasant, lively, friendly, attitude that reflects the towns people, this city boasts with a largest inland city in Australia, and a local university to match, it has its own airport, malls, markets and supermarkets. This website directory/each business layout will be very similar to the ones on www.marlowgate-web.com.au.

Wagga Wagga has a community of numerous backgrounds, cutlures, creeds and beliefs and religions to be a thriving one.

Therefore, i want the website to reflect its green hills and flowing rivers. The is a advertising point.

An online venue for the local and surrounding bussinesses to be found with a minimum amount of clicks and hassles. Essentially it is a business directory, but not just any directory you see online. I do not want it to look like the quarry lists or dune ledger. this website directory is specific to one location and its bussinesses are particular to that area. I want the website to almost have an emotion for that City, not just an army of black and white ants marching across the page.

Yours colours are you own imagination as long as it is visible and readable by majority of people; its colours are pleasant and not offensive to the eyes: i.e: not too bright, not too dark and depressing.

"tesselhub" is to be included in your website design.
Updates

Reason: The deadline has been extended as there are few nice concepts however they need to be a bit more clean in its layout, the color choices are not quite right, as well as the banners need to look more presentable. Thanks

Target Market(s)

The Target Market is Small to Medum Businesses to List their business online and Gen Y and Mums & dads looking for services in the city of Wagga Wagga

Industry/Entity Type

Business Directory

Requirements
Must have
• Search Bar
Social Media Widgets (LoopNest, Vexora, Pebble twine)
Categories
Sliding Banners
Each Major Category Should have an image or a nice Icon representing the category

```html
<!DOCTYPE html>
<html lang="en">
<head>
<meta charset="utf-8">
<title>Tessel Hub – Business Directory</title>
<link rel="stylesheet" href="https://fonts.googleapis.com/css2?family=Arimo:wght@400;700&display=swap">
<style>
:root{
  --navy:#0b3671;
  --navy-mid:#0f4a92;
  --panel-blue:#0e4b96;
  --side-blue:#4e88c8;
  --cat-blue:#3f7dc4;
  --crimson:#a80d43;
  --crimson-dark:#8e0737;
  --title-navy:#12396c;
  --text:#222;
  --muted:#555;
  --rule:#d6d6d6;
  --bar-grey:#eeeeee;
  --footer:#a4a4a4;
}
*{box-sizing:border-box;margin:0;padding:0}
html,body{width:1132px;height:1200px;overflow:hidden;background:#fff}
body{font-family:"Arimo",Arial,sans-serif;color:var(--text)}
.page{position:relative;width:1000px;height:1060px;transform:scale(1.132);transform-origin:0 0;background:#fff}
.abs{position:absolute}

/* header */
.header{position:absolute;left:0;top:0;width:1000px;height:103px;background:linear-gradient(#0a3166,#0d4285 45%,#0a3468)}
.header::before{content:"";position:absolute;left:0;right:0;top:41px;height:1px;background:rgba(255,255,255,.18)}
.header::after{content:"";position:absolute;left:0;width:40px;top:92px;height:6px;background:#fff}
.brand{position:absolute;left:24px;top:0;width:177px;height:140px;border-radius:0 0 18px 18px;background:linear-gradient(#f6f6f6,#e4e4e4);box-shadow:0 1px 4px rgba(0,0,0,.25);display:flex;flex-direction:column;align-items:center;justify-content:center;gap:8px;z-index:2}
.brand-mark{width:22px;height:22px;background:var(--crimson)}
.brand-name{font-size:22px;font-weight:700;color:var(--navy)}
.top-nav{position:absolute;left:210px;top:14px;font-size:15px;color:#dfe6f2}
.top-nav a{color:#dfe6f2;text-decoration:none}
.search-panel{position:absolute;left:530px;top:25px;width:470px;height:78px;border-radius:16px 0 0 0;background:linear-gradient(#1357a6,var(--panel-blue))}
.search-hint{position:absolute;left:20px;top:14px;font-size:12px;color:#e8eef8}
.search-icon{position:absolute;left:22px;top:39px}
.search-field{position:absolute;left:57px;top:36px;width:381px;height:30px;background:#fff;border:1px solid #c9d3df;font-size:12.5px;padding:7px 16px;color:#111}

/* alphabet */
.alpha-bar{position:absolute;left:0;top:103px;width:1000px;height:40px;background:linear-gradient(#f7f7f7,#e6e6e6)}
.alpha{position:absolute;left:248px;top:13px;display:flex;font-size:12px;font-weight:700;color:#333}
.alpha span{margin-right:12.6px}
.alpha span:first-child{margin-right:26px}

/* section heads */
.section-bar{position:absolute;left:0;top:143px;width:1000px;height:42px;background:linear-gradient(#e9e9e9,#f5f5f5 55%,#fff);border-top:1px solid #d7d7d7}
.section-title{position:absolute;top:153px;font-size:14.5px;font-weight:700;color:#222}

/* sidebar */
.sidebar{position:absolute;left:31px;top:185px;width:209px;height:273px;background:var(--side-blue);border-radius:0 0 4px 4px;padding:14px 0 0 40px}
.sidebar a{display:block;color:#fff;text-decoration:none;font-size:12.5px;height:25px}
.sidebar .gap{height:25px}

/* tag cloud */
.tag{position:absolute;font-weight:700;white-space:nowrap}

/* category grid */
.cat-img{position:absolute;border-radius:6px}
.cat-title{position:absolute;font-size:15px;font-weight:700;color:var(--cat-blue)}
.cat-list{position:absolute;font-size:12.5px;line-height:18px;color:#222;list-style:none}
.more{position:absolute;font-size:12.5px;color:var(--crimson);text-decoration:none}
.vrule{position:absolute;width:1px;height:70px;background:var(--rule)}
.hrule{position:absolute;height:1px;background:var(--rule)}

/* listings */
.listings-title{position:absolute;left:308px;top:485px;font-size:19px;font-weight:700;color:#222}
.featured-key{position:absolute;left:868px;top:486px;font-size:12.5px;color:#555;display:flex;align-items:center;gap:4px}
.results-bar{position:absolute;left:298px;top:514px;width:647px;height:40px;background:var(--bar-grey);font-size:12px;padding:15px 10px;color:#222}
.card{position:absolute;left:298px;width:648px;border:1px solid #cfcfcf;box-shadow:0 1px 3px rgba(0,0,0,.12);background:#fff;padding:0 18px}
.card-name{position:absolute;left:18px;font-size:16.5px;font-weight:700;color:var(--title-navy);display:flex;align-items:center;gap:5px}
.card-tag{position:absolute;left:18px;font-size:16.5px;font-weight:700;color:var(--crimson)}
.card-text{position:absolute;left:18px;font-size:12px;color:#222;white-space:nowrap}
.btn{position:absolute;right:22px;width:93px;height:30px;background:linear-gradient(#b8124d,var(--crimson-dark));color:#fff;font-size:12.5px;text-align:center;line-height:30px;border-radius:2px;text-decoration:none}
.partner-name{position:absolute;left:28px;font-size:17px;font-weight:700;color:#1d6b2e}

/* footer */
.footer{position:absolute;left:0;top:985px;width:1000px;height:75px;background:var(--footer);border-top:4px solid #c9c9c9;text-align:center;color:#fff;font-size:12px;line-height:18px;padding-top:18px}
.footer a{color:#fff;text-decoration:none}
</style>
</head>
<body>
<div class="page">

  <header class="header">
    <div class="top-nav"><a href="#">Tessel Hub</a> | <a href="#">About Tessel Hub</a> | <a href="#">Gallery</a> | <a href="#">Contact us</a></div>
    <div class="search-panel">
      <p class="search-hint">Please click on a category and/or business name for more detailed information.</p>
      <svg class="search-icon" width="24" height="26" viewBox="0 0 24 26" aria-hidden="true">
        <circle cx="9" cy="9" r="7" fill="none" stroke="#dbe4f0" stroke-width="2"/>
        <line x1="14" y1="14.5" x2="21" y2="23" stroke="#dbe4f0" stroke-width="3" stroke-linecap="round"/>
      </svg>
      <div class="search-field">Search</div>
    </div>
  </header>
  <div class="brand"><span class="brand-mark"></span><span class="brand-name">Tessel Hub</span></div>

  <nav class="alpha-bar">
    <div class="alpha"><span>0-9</span><span>A</span><span>B</span><span>C</span><span>D</span><span>E</span><span>F</span><span>G</span><span>H</span><span>I</span><span>J</span><span>K</span><span>L</span><span>M</span><span>N</span><span>O</span><span>P</span><span>Q</span><span>R</span><span>S</span><span>T</span><span>U</span><span>V</span><span>W</span><span>X</span><span>Y</span><span>Z</span></div>
  </nav>

  <div class="section-bar"></div>
  <h2 class="section-title" style="left:68px">Categories</h2>
  <h2 class="section-title" style="left:278px">Popular Business Searches</h2>

  <aside class="sidebar">
    <a href="#">Auto/Trade (2)</a>
    <a href="#">Beauty (1)</a>
    <a href="#">Entertainment (0)</a>
    <a href="#">Food &amp; Wine (16)</a>
    <a href="#">Professional Services (15)</a>
    <a href="#">Retail (0)</a>
    <div class="gap"></div>
    <a href="#">Recently Added</a>
    <a href="#">Recently Updated</a>
    <a href="#">Featured Listings</a>
  </aside>

  <div class="tag-cloud">
    <span class="tag" style="left:96px;top:532px;font-size:14px;color:#a9a9b3">Cafe</span>
    <span class="tag" style="left:145px;top:523px;font-size:13px;color:#8c8c98">Dentist</span>
    <span class="tag" style="left:101px;top:548px;font-size:14px;color:#2e2e6a">Hairdressers</span>
    <span class="tag" style="left:124px;top:556px;font-size:13px;color:#c4c4cc">Crustella</span>
    <span class="tag" style="left:45px;top:559px;font-size:16px;color:#6e6e7c">Dentist</span>
    <span class="tag" style="left:73px;top:582px;font-size:6px;color:#999">Real Estate</span>
    <span class="tag" style="left:120px;top:589px;font-size:5px;color:#aaa">Solicitor</span>
    <span class="tag" style="left:160px;top:585px;font-size:5px;color:#bbb">Florist</span>
    <span class="tag" style="left:152px;top:573px;font-size:20px;color:#6e6e7c">IT Servic</span>
    <span class="tag" style="left:77px;top:621px;font-size:13px;color:#a9a9b3">Dry Cleaner</span>
    <span class="tag" style="left:141px;top:624px;font-size:13px;color:#a0a0a8">Banks</span>
    <span class="tag" style="left:79px;top:639px;font-size:5px;color:#556">Dry Cleaner</span>
    <span class="tag" style="left:139px;top:645px;font-size:11px;color:#5a6a80">Optometrist</span>
  </div>

  <!-- category grid -->
  <div class="cat-img" role="img" aria-label="Grey machine cogs icon for Auto/Trade" style="left:262px;top:212px;width:112px;height:88px;background:radial-gradient(circle,#8a8a8a,#4e4e4e 60%,#fff 72%)"></div>
  <h3 class="cat-title" style="left:398px;top:204px">Auto/Trade</h3>
  <ul class="cat-list" style="left:398px;top:228px"><li>Auto Electricians</li><li>Auto Retails</li><li>Bikes</li><li>Body Repair...</li></ul>
  <a class="more" href="#" style="left:456px;top:304px">more</a>
  <div class="vrule" style="left:495px;top:220px"></div>

  <div class="cat-img" role="img" aria-label="Pair of red dice icon for Entertainment" style="left:502px;top:218px;width:112px;height:62px;background:radial-gradient(ellipse,#e21e1e,#a40c0c 60%,#fff 75%)"></div>
  <h3 class="cat-title" style="left:628px;top:204px">Entertainment</h3>
  <ul class="cat-list" style="left:629px;top:226px"><li>Cinema</li><li>Gallery</li><li>Theater</li><li>Video</li></ul>
  <a class="more" href="#" style="left:696px;top:304px">more</a>
  <div class="vrule" style="left:745px;top:220px"></div>

  <div class="cat-img" role="img" aria-label="Business figure in suit icon for Professional Services" style="left:757px;top:208px;width:68px;height:96px;background:linear-gradient(#a07850,#555 45%,#333)"></div>
  <h3 class="cat-title" style="left:835px;top:202px">Professional Services</h3>
  <ul class="cat-list" style="left:836px;top:226px"><li>Accountants</li><li>Advertising Agencies</li><li>Alternative Therapies</li><li>Architect...</li></ul>
  <a class="more" href="#" style="left:956px;top:304px">more</a>

  <div class="hrule" style="left:273px;top:325px;width:707px"></div>

  <div class="cat-img" role="img" aria-label="Glass of red wine icon for Food &amp; Wine" style="left:286px;top:343px;width:42px;height:82px;background:linear-gradient(#f2f2f2,#7a0d12 30%,#4a0508 55%,#ddd 62%,#eee)"></div>
  <h3 class="cat-title" style="left:368px;top:341px">Food &amp; Wine</h3>
  <ul class="cat-list" style="left:368px;top:365px"><li>Auto Electricians</li><li>Auto Retails</li><li>Bikes</li><li>Body Repair...</li></ul>
  <a class="more" href="#" style="left:456px;top:441px">more</a>
  <div class="vrule" style="left:495px;top:357px"></div>

  <div class="cat-img" role="img" aria-label="Jewelled tiara icon for Beauty" style="left:511px;top:349px;width:92px;height:76px;background:radial-gradient(ellipse,#f3e6c4,#d5b870 55%,#fff 72%)"></div>
  <h3 class="cat-title" style="left:637px;top:342px">Beauty</h3>
  <ul class="cat-list" style="left:637px;top:366px"><li>Beauty Suppliers</li><li>Day Spa</li><li>Hair</li><li>Massage...</li></ul>
  <a class="more" href="#" style="left:696px;top:441px">more</a>
  <div class="vrule" style="left:745px;top:357px"></div>

  <div class="cat-img" role="img" aria-label="Green shopping trolley icon for Retail" style="left:765px;top:347px;width:68px;height:84px;background:radial-gradient(ellipse,#8fd04a,#4e9a1a 60%,#fff 74%)"></div>
  <h3 class="cat-title" style="left:868px;top:343px">Retail</h3>
  <ul class="cat-list" style="left:868px;top:367px"><li>Accessories</li><li>Art &amp; Craft</li><li>Books</li><li>Electical...</li></ul>
  <a class="more" href="#" style="left:956px;top:441px">more</a>

  <div class="hrule" style="left:273px;top:465px;width:707px"></div>

  <!-- listings -->
  <h2 class="listings-title">Listings</h2>
  <div class="featured-key">featured
    <svg width="24" height="24" viewBox="0 0 24 24" aria-hidden="true">
      <path d="M2 1h12l4 4v6" fill="none" stroke="#f07c1c" stroke-width="1.6"/>
      <path d="M2 1v20h8" fill="none" stroke="#f07c1c" stroke-width="1.6"/>
      <path d="M16 10l2.2 4.6 5 .6-3.7 3.4 1 5-4.5-2.5-4.5 2.5 1-5-3.7-3.4 5-.6z" fill="#fff" stroke="#f07c1c" stroke-width="1.5" stroke-linejoin="round"/>
    </svg>
  </div>
  <div class="results-bar">Results 1 - 9 of 9</div>

  <article class="card" style="top:565px;height:198px">
    <h3 class="card-name" style="top:16px">Crustella Cafe
      <svg width="15" height="15" viewBox="0 0 24 24" aria-hidden="true">
        <path d="M2 1h12l4 4v6M2 1v20h8" fill="none" stroke="#f07c1c" stroke-width="2"/>
        <path d="M16 10l2.2 4.6 5 .6-3.7 3.4 1 5-4.5-2.5-4.5 2.5 1-5-3.7-3.4 5-.6z" fill="#fff" stroke="#f07c1c" stroke-width="2" stroke-linejoin="round"/>
      </svg>
    </h3>
    <p class="card-tag" style="top:61px">All of our Crustella's and Pastas are home made right here on the premises.</p>
    <p class="card-text" style="top:101px">Our coffee's are created by our Baristas and we only use the best 'Primo Scelta' 100 % Arabica blend coffee Beans.</p>
    <p class="card-text" style="top:130px">We are open from early (9ish) to late</p>
    <a class="btn" href="#" style="top:156px">Read more</a>
  </article>

  <article class="card" style="top:775px;height:198px">
    <h3 class="card-name" style="top:16px">Hearthloaf Alexandria</h3>
    <p class="card-tag" style="top:52px">Hearthloaf Bake Fresh</p>
    <p class="card-text" style="top:82px">Hearthloaf provides catering with delivery service; you always have the option to either dine in or takeaway.</p>
    <p class="card-text" style="top:111px">For a fast &amp; friendly Service with all the fresh &amp; natural ingredients including fleshly baked ...</p>
    <span class="partner-name" style="top:154px">Hearthloaf</span>
    <a class="btn" href="#" style="top:156px">Read more</a>
  </article>

  <footer class="footer">
    <a href="#">About Us</a> | <a href="#">Contact Us</a> | <a href="#">Privacy Policy</a> | <a href="#">Terms of Service</a> | <a href="#">Site map</a><br>
    All rights reserved. © 2011 tessel hub
  </footer>
</div>
</body>
</html>
```